Corvane Holdings , new business card design

investment firm with corporate clients . need double sided business card , vertical and horizontal options ,logo must be clear. prefer pantone colors only and sharp design. website also www.corvane.ae

Khalid Bin Tarrafi
Managing Director
Tel. +971 4 387 2940
Mobile +971 50 518 2403
khalid@corvane.ae
Q-Span Plaza, officw 18-B07, Warqa Gardens, Dubai

Contact Information for Business Card

Khalid Bin Tarrafi
Managing Director

Font styles to use
Serif

Colors

Designer to choose colors to be used in the design.

```html
<!DOCTYPE html>
<html lang="en">
<head>
<meta charset="utf-8">
<title>Corvane Holdings – Business Card</title>
<link rel="stylesheet" href="https://fonts.googleapis.com/css2?family=Oswald:wght@500&family=Roboto:wght@300;400&display=swap">
<style>
  :root {
    --backdrop: #e3e3e3;
    --card-white: #f7f7f7;
    --card-black: #0d0d11;
    --accent-blue: #4a77a3;
    --ink: #111114;
    --ink-soft: #555558;
    --paper: #ffffff;
  }
  * { margin: 0; padding: 0; box-sizing: border-box; }
  html, body {
    width: 1200px; height: 960px; overflow: hidden;
    background: var(--backdrop);
    font-family: "Roboto", Arial, sans-serif;
  }
  .canvas { position: relative; width: 1200px; height: 960px; }

  .card { position: absolute; width: 600px; height: 342px; }
  .card--front { left: 152px; top: 125px; background: var(--card-white); }
  .card--back  { left: 452px; top: 500px; background: var(--card-black); }

  .edge-stripe { position: absolute; left: 0; width: 14px; background: var(--ink); }
  .edge-stripe--top { top: 0; height: 212px; }
  .edge-stripe--bottom { top: 262px; height: 80px; }
  .edge-ticks { position: absolute; left: 0; top: 219px; width: 14px; }
  .edge-ticks span { display: block; height: 5px; background: var(--accent-blue); margin-bottom: 7px; }

  .wordmark {
    position: absolute; font-weight: 300; white-space: nowrap;
    letter-spacing: 0.22em; text-transform: uppercase;
  }
  .card--front .wordmark { right: 55px; top: 70px; font-size: 25px; color: var(--ink); }
  .card--back .wordmark { left: 0; right: 0; top: 156px; text-align: center; font-size: 27px; color: var(--paper); padding-left: 0.22em; }

  .holder { position: absolute; left: 41px; top: 219px; }
  .holder__name {
    font-family: "Oswald", "Arial Narrow", sans-serif; font-weight: 500;
    font-size: 18px; color: var(--accent-blue); letter-spacing: 0.01em; line-height: 24px;
  }
  .holder__title { font-size: 14px; color: var(--ink); letter-spacing: 0.03em; line-height: 18px; }

  .address {
    position: absolute; right: 57px; top: 178px; text-align: right;
    font-size: 14px; line-height: 18px; color: var(--ink-soft);
  }
  .contacts { position: absolute; right: 57px; top: 223px; list-style: none; }
  .contacts li {
    display: flex; justify-content: flex-end; align-items: center; gap: 12px;
    font-size: 14px; line-height: 19.5px; color: var(--ink-soft);
  }
  .contacts svg { width: 14px; height: 14px; fill: var(--accent-blue); }

  .back-url {
    position: absolute; left: 0; right: 0; top: 285px; text-align: center;
    font-size: 15px; color: var(--paper); letter-spacing: 0.5em; padding-left: 0.5em;
  }
</style>
</head>
<body>
<main class="canvas">
  <section class="card card--front" aria-label="Business card front">
    <div class="edge-stripe edge-stripe--top"></div>
    <div class="edge-ticks"><span></span><span></span><span></span></div>
    <div class="edge-stripe edge-stripe--bottom"></div>

    <div class="wordmark">Corvane Holdings</div>

    <div class="holder">
      <p class="holder__name">KHALID BIN TARRAFI</p>
      <p class="holder__title">MANAGING DIRECTOR</p>
    </div>

    <address class="address" style="font-style:normal">
      Q-Span Plaza, officw 18-B07<br>Warqa Gardens, Dubai
    </address>

    <ul class="contacts">
      <li>+971 4 387 2940
        <svg viewBox="0 0 16 16" aria-hidden="true"><path d="M3.6 1.2l2.3 2.6-1.2 2c.8 1.9 2.2 3.3 4.1 4.2l2-1.3 2.6 2.3-1.1 2.5C7 13.9 2 9 1.2 3.3z"/></svg></li>
      <li>+971 50 518 2403
        <svg viewBox="0 0 16 16" aria-hidden="true"><path d="M4.5 1h7a1 1 0 0 1 1 1v12a1 1 0 0 1-1 1h-7a1 1 0 0 1-1-1V2a1 1 0 0 1 1-1zm.6 1.8v9.4h5.8V2.8zM8 12.8a.8.8 0 1 0 0 1.6.8.8 0 0 0 0-1.6z"/></svg></li>
      <li>khalid@corvane.ae
        <svg viewBox="0 0 16 16" aria-hidden="true"><path d="M1 3.5h14v.8L8 8.6 1 4.3zm0 2.2l7 4.3 7-4.3v6.8H1z"/></svg></li>
      <li>www.corvane.ae
        <svg viewBox="0 0 16 16" aria-hidden="true"><circle cx="8" cy="8" r="7"/><path d="M5 4.5c1.2.3 1.4 1.6 2.6 1.8.9.2.6 1.6-.3 1.8-1 .3-1.5 1.5-.8 2.3.5.6-.1 1.8-.9 1.9C4 11 3.2 8.6 3.6 6.5 3.8 5.4 4.2 4.4 5 4.5zm5.5-.8c1 .5 1.9 1.6 2 2.8-.7.3-1.7-.2-1.9-1-.2-.6-.6-1.2-.1-1.8z" fill="#f7f7f7"/></svg></li>
    </ul>
  </section>

  <section class="card card--back" aria-label="Business card back">
    <div class="wordmark">Corvane Holdings</div>
    <p class="back-url">www.corvane.ae</p>
  </section>
</main>
</body>
</html>
```